We (R. T. Galvin & Partners, Inc.) are an executive Search firm based in Los Angeles that is exclusively focused in the Med Tech and Health Tech arenas.   I need a logo to communicate that we are a high end search firm, but also that we are focused in the medicine and science arenas called health tech and med tech.  Many of our clients have robotics and artificial intelligence type products, so it is very technology forward.  I tend to gravitate towards clean, sharp aesthetic as opposed to something that is really over the top.
Attached are files with my logo in two different layouts.  In addition to the letterhead and envelope, I also will need an electronic letterhead in Microsoft Word.  I tend to
I look forward to seeing the designs and just let me know if you have any questions.
Dale

```html
<!DOCTYPE html>
<html lang="en">
<head>
<meta charset="utf-8">
<title>R. T. Galvin &amp; Partners, Inc. — Stationery</title>
<link href="https://fonts.googleapis.com/css2?family=Poppins:wght@500&family=Roboto:wght@300;400&display=swap" rel="stylesheet">
<style>
  :root {
    --backdrop: #6e6e6e;
    --paper: #f3f3f3;
    --brand-blue: #4ea1db;
    --ink: #111418;
    --body-ink: #3c3f44;
    --white: #ffffff;
  }
  * { box-sizing: border-box; margin: 0; padding: 0; }
  html, body { width: 1200px; height: 993px; overflow: hidden; background: var(--backdrop); }
  .canvas { position: relative; width: 1200px; height: 993px; }

  .pattern-sheet {
    position: absolute; left: 244px; top: 50px; width: 562px; height: 790px;
    background: linear-gradient(135deg, #4a9edb, #58a9e0);
  }

  .letterhead {
    position: absolute; left: 83px; top: 99px; width: 561px; height: 790px;
    background: var(--paper); box-shadow: 0 0 0 1px rgba(0,0,0,.08);
    font-family: "Roboto", sans-serif;
  }
  .brand { position: absolute; display: flex; align-items: center; gap: 12px; }
  .brand__dot { border-radius: 50%; background: var(--brand-blue); flex: none; }
  .brand__name {
    font-family: "Poppins", sans-serif; font-weight: 500; color: var(--ink);
    line-height: 1.15; letter-spacing: .2px;
  }
  .letterhead .brand { left: 170px; top: 168px; }
  .letterhead .brand__dot { width: 34px; height: 34px; }
  .letterhead .brand__name { font-size: 19px; }

  .letter { position: absolute; left: 53px; top: 200px; width: 456px; color: var(--body-ink); font-size: 11.2px; font-weight: 300; line-height: 13.6px; }
  .letter__greeting { margin-bottom: 27px; }
  .letter p { margin-bottom: 13.6px; text-align: justify; }
  .letter__closing { margin-top: 27px; }
  .letter__signature { width: 58px; height: 24px; margin-top: 16px; background: linear-gradient(90deg, #e6e7ea, #eef0f2); border-radius: 3px; }

  .contact-band {
    position: absolute; left: 46px; top: 727px; width: 476px; height: 36px;
    background: var(--brand-blue); color: var(--white);
    display: flex; align-items: center; padding-left: 16px; font-size: 9px; line-height: 9.5px;
  }
  .contact-band__item { display: flex; align-items: center; gap: 6px; padding-right: 14px; margin-right: 14px; border-right: 1px solid rgba(255,255,255,.7); height: 24px; }
  .contact-band__item:last-child { border-right: 0; }
  .contact-band__icon { width: 15px; height: 15px; flex: none; }

  .envelope-front {
    position: absolute; left: 514px; top: 250px; width: 574px; height: 277px;
    background: var(--paper); box-shadow: 0 0 0 1px rgba(0,0,0,.08);
    font-family: "Roboto", sans-serif;
  }
  .envelope-front .brand { left: 40px; top: 36px; gap: 8px; }
  .envelope-front .brand__dot { width: 20px; height: 20px; }
  .envelope-front .brand__name { font-size: 13px; }
  .return-address { position: absolute; left: 88px; top: 70px; font-size: 10px; line-height: 12.5px; color: var(--body-ink); }

  .envelope-back {
    position: absolute; left: 511px; top: 576px; width: 574px; height: 277px;
    background: var(--paper); box-shadow: 0 0 0 1px rgba(0,0,0,.08);
  }
  .envelope-back__flap { position: absolute; left: 0; top: 0; }
</style>
</head>
<body>
<div class="canvas">

  <div class="pattern-sheet" role="img" aria-label="Blue second sheet covered with a repeating light dot pattern"></div>

  <section class="letterhead">
    <div class="brand">
      <span class="brand__dot"></span>
      <span class="brand__name">R. T. GALVIN<br>&amp; PARTNERS INC.</span>
    </div>

    <div class="letter">
      <p class="letter__greeting">Dear Mr. Carter,</p>
      <p>Lorem ipsum dolor sit amet, consectetur adipiscing elit. Donec orci purus, luctus sim eu, iaculis sed purus. Vivamus faucibus, ipsum nec aliquet viverra, leo massa tum ligula, sit amet sagittis enim ligula quis arcu. Nam egestas tortor id nisi porta. In tortor ante, ultricies in suscipit a, tempus non massa. Vivamus et auctor massa nulla. Phasellus nec eros mauris, et scelerisque orci.</p>
      <p>Donec malesuada orci vitae nulla accumsan porta a id massa. Quisque ac magna sit amet fringilla. Maecenas consequat, magna eget tincidunt semper, rutrum mi, id feugiat ante nisi eu risus. Vestibulum nunc orci, rhoncus a placerat in mi. Cras mattis varius eros, vel fringilla nisi suscipit eget. Quisque scelerisque at porttitor.</p>
      <p>Sed id augue vitae urna euismod commodo aliquet a quam. Pellentesque arcu malesuada ut, consequat et diam. Nullam erat sem, rhoncus id ullamcorper vel, arcu. In ultricies ultricies nulla, ut rutrum nisi iaculis at. Donec eu magna a metus ornare faucibus. Fusce aliquet faucibus ultricies. Morbi semper, est id tincidunt gravida, sem arcu adipiscing lacus, ac bibendum nulla leo eu purus. Quisque nec diam sed risus consectetur a accumsan quis quis nibh. Vestibulum id purus lorem.</p>
      <p>It is a long established fact that a reader will be distracted by the readable content when looking at its layout. The point of using Lorem Ipsum is that it has a more normal distribution of letters, as opposed to using 'Content here, content here', making it like readable English. Many desktop publishing packages</p>
      <p class="letter__closing">Sincerely,</p>
      <div class="letter__signature" role="img" aria-label="Handwritten signature"></div>
    </div>

    <footer class="contact-band">
      <div class="contact-band__item">
        <svg class="contact-band__icon" viewBox="0 0 16 16"><rect width="16" height="16" rx="2" fill="#fff"/><path d="M8 3.2a3 3 0 0 0-3 3c0 2.3 3 5.8 3 5.8s3-3.5 3-5.8a3 3 0 0 0-3-3z" fill="#4ea1db"/><circle cx="8" cy="6.2" r="1.1" fill="#fff"/></svg>
        <span>412 Harbor Crest Drive<br>Pasadena, California 91101</span>
      </div>
      <div class="contact-band__item">
        <svg class="contact-band__icon" viewBox="0 0 16 16"><rect width="16" height="16" rx="2" fill="#fff"/><path d="M5.2 3.5l1.6 1.9-.9 1.3c.6 1.3 1.6 2.3 2.9 2.9l1.3-.9 1.9 1.6-.9 1.7c-3.6-.3-6.5-3.2-6.8-6.8z" fill="#4ea1db"/></svg>
        <span>555-214-7730<br>555-318-4426</span>
      </div>
      <div class="contact-band__item">
        <svg class="contact-band__icon" viewBox="0 0 16 16"><rect width="16" height="16" rx="2" fill="#fff"/><circle cx="8" cy="8" r="4.5" fill="none" stroke="#4ea1db" stroke-width="1.2"/><path d="M3.5 8h9M8 3.5c-2 2.5-2 6.5 0 9M8 3.5c2 2.5 2 6.5 0 9" fill="none" stroke="#4ea1db" stroke-width="1"/></svg>
        <span>info@rtgalvin.com<br>www.rtgalvin.com</span>
      </div>
    </footer>
  </section>

  <section class="envelope-front">
    <div class="brand">
      <span class="brand__dot"></span>
      <span class="brand__name">R. T. GALVIN<br>&amp; PARTNERS INC.</span>
    </div>
    <p class="return-address">412 Harbor Crest Drive<br>Pasadena, California 91101</p>
  </section>

  <section class="envelope-back">
    <svg class="envelope-back__flap" width="574" height="96" viewBox="0 0 574 96">
      <path d="M0 0H574L560 60Q553 94 520 94H54Q21 94 14 60Z" fill="#4ea1db"/>
    </svg>
  </section>

</div>
</body>
</html>
```